Project Overview:
We are looking to create a website for a monthly subscription IPTV service in WordPress. The website should provide a seamless user experience for customers to sign up for the service and manage their account information. We need the following pages: Home Page, Product Page, Sign-Up Page, and Account Information Page.

Home Page:
The Home Page design should be simple and clean, with a dark theme and minimalistic design elements. We would like to include graphics of popular movie shows displayed on multiple devices. The page should highlight the key benefits and features of our service and provide a clear call-to-action for visitors to sign up.

Product Page:
The Product Page should provide detailed information about our subscription tiers and pricing plans. It should highlight the key features of each plan and provide a clear comparison between them. The page should also include a call-to-action button for visitors to sign up.

Sign-Up Page:
The Sign-Up Page is the conversion page where members will sign up for the service. It should collect the following information: Name, Phone Number, Email, Password, and Payment Information. The design should be simple, intuitive, and easy to use. It should highlight the benefits of our service and provide a clear call-to-action for visitors to sign up.

Account Information Page:
The Account Information Page should allow members to view and manage their account details. It should include the following information: Profile Image, Contact Details, Password Management, Payment Information Management, and Membership Expiration Date. The design should be user-friendly, intuitive, and easy to navigate.

Goals: The primary goal of the website is to provide an easy-to-use portal for customers to sign up for the service and manage their account information. The website should be user-friendly and visually appealing to attract potential customers.

Scope: The scope of the project includes designing a home page, a sign-up page, an account information page, and a payment information page. The website should be designed to be responsive and accessible on desktop and mobile devices.

Design Preferences: The design should be clean, modern, and visually appealing. The use of a color palette that is consistent with the brand identity is recommended. The website should be easy to navigate and provide a clear call-to-action for users to sign up for the service.

FYI: The subscription service I am designing a website for is related to an IPTV service. IPTV stands for Internet Protocol Television, which is a digital television broadcasting protocol that uses the internet to deliver TV programs and videos to viewers. The website will allow customers to sign up for the IPTV service and access their account information such as user name and password, membership tier, name, and payment details. Please let me know if you have any further questions, and I would be happy to provide more details. Thank you!

Dear Designers,

Thank you for your participation in our project. After reviewing the designs received so far, we have decided to update the brief to better reflect our needs and preferences. We apologize for any confusion this may cause, but we believe that these changes will result in better design submissions and a more successful project overall.

The updated brief is as follows:

We are looking to create a website for WordPress.

Also, here is the updated Brief.

Project Title: WordPress Website Design for Monthly Subscription IPTV Service

Project Overview:
We are looking to create a website for a monthly subscription IPTV service. The website should provide a seamless user experience for customers to sign up for the service and manage their account information. We need the following pages: Home Page, Product Page, Sign-Up Page, and Account Information Page.

Home Page:

Product Page:

Sign-Up Page:

Account Information Page:

Design Preferences:
We prefer a dark theme with minimalistic design elements and hits of our logo colors. The website should be easy to use and navigate, with clear calls-to-action and simple, intuitive forms. The design should be optimized for mobile devices and load quickly.

We hope that these updates provide you with a clearer understanding of our requirements and preferences. Please let us know if you have any questions or concerns. We look forward to seeing your revised designs.

Thank you again for your participation.
We will guarantee this project as soon as we see something we like that meets the updated requirements.

The website's target audience is individuals who are interested in subscribing to the monthly service.

4 page

• One item for sale and a client profile section.

```html
<!DOCTYPE html>
<html lang="en">
<head>
<meta charset="utf-8">
<title>VYNTRA – Subscription IPTV</title>
<link href="https://fonts.googleapis.com/css2?family=Open+Sans:wght@400;600;700;800&family=Lato:wght@400;700&display=swap" rel="stylesheet">
<style>
:root{
  --red:#f00000;
  --red-dark:#c80000;
  --black:#000;
  --ink:#2b2b2b;
  --grey:#6b6b6b;
  --light:#9a9a9a;
  --line:#d8d8d8;
  --white:#fff;
}
*{margin:0;padding:0;box-sizing:border-box}
html,body{width:1200px;height:3756px;overflow:hidden;background:var(--white)}
body{position:relative;font-family:"Lato",sans-serif;color:var(--ink)}
.abs{position:absolute}
.head{font-family:"Open Sans",sans-serif}

/* header */
.brand{left:117px;top:26px;font-family:"Open Sans",sans-serif;font-weight:800;font-size:64px;color:var(--red);letter-spacing:1px;line-height:1}
.call-icon{left:606px;top:46px;width:46px;height:46px;border:3px solid var(--red);border-radius:50%}
.call-label{left:666px;top:44px;font-family:"Open Sans",sans-serif;font-weight:600;font-size:15px}
.call-num{left:666px;top:64px;font-family:"Open Sans",sans-serif;font-weight:700;font-size:21px}
.social{top:59px;width:29px;height:29px;border-radius:50%;background:#8c8c8c}
.lang{left:981px;top:66px;font-family:"Open Sans",sans-serif;font-size:13px;font-weight:600}
.flag{left:1026px;top:60px;width:28px;height:28px;border-radius:50%;background:linear-gradient(180deg,#2f3f8f 0 45%,#e23 45% 60%,#fff 60% 70%,#e23 70%)}

/* nav */
.nav{left:0;top:130px;width:1200px;height:58px;background:var(--black)}
.nav ul{list-style:none;display:flex;position:absolute;left:210px;top:0;height:58px}
.nav li{font-family:"Open Sans",sans-serif;font-weight:700;font-size:13.5px;color:var(--white);padding:0 12.5px;line-height:58px}
.nav li.active{background:var(--red);padding:0 15px}

/* hero */
.hero{left:0;top:188px;width:1200px;height:702px;background:linear-gradient(135deg,#2a2f3a 0%,#4a3a30 40%,#6a4a34 65%,#2c2a2c 100%)}
.hero-panel{left:254px;top:508px;width:690px;height:252px;background:rgba(0,0,0,.35)}
.hero-title{left:0;top:545px;width:1200px;text-align:center;font-family:"Open Sans",sans-serif;font-weight:700;font-size:60px;color:var(--white)}
.hero-sub{left:0;top:620px;width:1200px;text-align:center;font-family:"Open Sans",sans-serif;font-weight:700;font-size:20.5px;color:var(--white)}
.btn{background:var(--red);color:var(--white);font-family:"Open Sans",sans-serif;font-weight:700;font-size:14px;border-radius:24px;text-align:center;text-transform:uppercase}
.hero-btn{left:527px;top:665px;width:146px;height:47px;line-height:47px}
.arrow{top:480px;width:44px;height:44px;border-radius:50%;background:var(--white)}
.hero-curve{left:0;top:780px;width:1200px;height:112px}

/* about */
.hex{clip-path:polygon(25% 0,75% 0,100% 50%,75% 100%,25% 100%,0 50%)}
.about-label{left:625px;top:952px;font-family:"Open Sans",sans-serif;font-weight:700;font-size:24px;color:#8a8a8a}
.about-rule{left:625px;top:995px;width:76px;height:2px;background:#9ab}
.about-title{left:624px;top:1010px;font-family:"Open Sans",sans-serif;font-weight:700;font-size:38px;color:var(--red)}
.copy{font-size:14px;line-height:25.7px;color:var(--grey)}
.about-p1{left:627px;top:1070px;width:462px}
.about-p2{left:627px;top:1224px;width:462px}
.about-btn{left:628px;top:1295px;width:147px;height:44px;line-height:44px}

/* featured */
.feat-label{left:112px;top:1455px;font-family:"Open Sans",sans-serif;font-weight:700;font-size:25px}
.feat-box{top:1439px;width:165px;height:67px;background:var(--white);box-shadow:0 1px 8px rgba(0,0,0,.18)}
.feat-mark{position:absolute;left:56px;top:17px;width:54px;height:33px;border-radius:6px;background:#e6e6e6}

/* services */
.svc-bg{left:0;top:1598px;width:1200px;height:694px}
.svc-title{left:0;top:1722px;width:1200px;text-align:center;font-family:"Open Sans",sans-serif;font-weight:700;font-size:34px;color:var(--white)}
.svc-img{top:1808px;width:227px;height:217px}
.svc-card{top:1962px;width:201px;height:193px;background:var(--white);padding:22px 19px 0 19px}
.svc-card h3{font-family:"Open Sans",sans-serif;font-weight:700;font-size:17px;color:var(--ink);margin-bottom:8px;line-height:24px}
.svc-card p{font-size:11px;line-height:18px;color:var(--grey)}
.svc-btn{display:inline-block;margin-top:13px;width:93px;height:25px;line-height:25px;font-size:11px;border-radius:0}

/* tv */
.tv-img{left:0;top:2292px;width:598px;height:528px;background:linear-gradient(160deg,#1e1e26 0%,#3a2e2e 45%,#8a6a5a 75%,#c9a98a 100%)}
.tv-card{left:487px;top:2385px;width:602px;height:485px;background:var(--white);box-shadow:0 4px 24px rgba(0,0,0,.12);padding:60px 44px 0 50px}
.tv-card h2{font-family:"Open Sans",sans-serif;font-weight:700;font-size:34px;line-height:38px;color:var(--ink);margin-bottom:26px}
.tv-card p{text-align:justify;margin-bottom:25px}

/* subscription */
.sub-title{left:0;top:2965px;width:1200px;text-align:center;font-family:"Open Sans",sans-serif;font-weight:700;font-size:34px}
.field{height:40px;border-bottom:1px solid var(--line);font-size:14px;color:var(--grey);padding:9px 8px}
.card-ico{position:absolute;right:14px;top:14px;width:16px;height:11px;border:2px solid #777;border-top-width:4px;border-radius:2px}
.sub-btn{left:527px;top:3190px;width:147px;height:46px;line-height:46px}

/* footer */
.foot-shape{left:0;top:3300px;width:1200px;height:456px}
.foot-brand{left:112px;top:3462px;font-family:"Open Sans",sans-serif;font-weight:800;font-size:36px;color:var(--red);line-height:1}
.foot-text{left:112px;top:3510px;width:250px;font-size:14px;line-height:25.7px;color:var(--white)}
.foot-h{top:3462px;font-family:"Open Sans",sans-serif;font-weight:600;font-size:18px;color:var(--white)}
.foot-h::after{content:"";display:block;width:36px;height:2px;background:var(--red);margin-top:6px}
.foot-list{list-style:none;top:3518px}
.foot-list li{font-size:14px;line-height:25.7px;color:var(--white)}
.foot-list li::before{content:"»";margin-right:8px}
.ct-row{left:886px;font-size:14px;line-height:25.7px;color:var(--white);padding-left:37px;width:210px}
.ct-ico{position:absolute;left:0;top:2px;width:24px;height:24px;background:var(--red)}
.foot-rule{left:112px;top:3679px;width:976px;height:1px;background:#555}
.copyright{left:0;top:3707px;width:1200px;text-align:center;font-size:14px;color:var(--white)}
</style>
</head>
<body>

<!-- header -->
<div class="abs brand">VYNTRA</div>
<div class="abs call-icon">
  <svg width="40" height="40" viewBox="0 0 40 40"><path d="M13 10l5 5-3 3c1 3 4 6 7 7l3-3 5 5-3 4c-9-1-17-9-18-18z" fill="#f00000"/></svg>
</div>
<div class="abs call-label">Call us Today :</div>
<div class="abs call-num">+1 888 888 8888</div>
<div class="abs social" style="left:852px"></div>
<div class="abs social" style="left:886px"></div>
<div class="abs social" style="left:920px"></div>
<div class="abs lang">Eng ˅</div>
<div class="abs flag" role="img" aria-label="English language flag"></div>

<nav class="abs nav">
  <ul>
    <li class="active">HOME</li><li>OUR STORY</li><li>SERVICES</li><li>WHY US?</li><li>REVIEWS</li><li>TV PROGRAMS</li><li>BLOG</li><li>VIDEOS</li><li>CONTACT</li>
  </ul>
</nav>

<!-- hero -->
<div class="abs hero" role="img" aria-label="Friends relaxing in a cosy living room at night, watching TV together"></div>
<div class="abs hero-panel"></div>
<div class="abs hero-title">VYNTRA</div>
<div class="abs hero-sub">SUBSCRIPTION-BASED WEBSITE FOR A MONTHLY SERVICE</div>
<div class="abs btn hero-btn">Signup</div>
<div class="abs arrow" style="left:66px"><svg width="44" height="44"><path d="M25 15l-7 7 7 7" stroke="#c08a2a" stroke-width="3" fill="none"/></svg></div>
<div class="abs arrow" style="left:1089px"><svg width="44" height="44"><path d="M19 15l7 7-7 7" stroke="#c08a2a" stroke-width="3" fill="none"/></svg></div>
<svg class="abs hero-curve" viewBox="0 0 1200 112" preserveAspectRatio="none">
  <path d="M0 112 L0 100 Q600 10 1200 100 L1200 112 Z" fill="#fff"/>
  <path d="M110 92 Q600 -6 1090 90 Q600 22 110 92 Z" fill="#f00000"/>
</svg>

<!-- about -->
<div class="abs hex" style="left:95px;top:953px;width:272px;height:247px;background:linear-gradient(135deg,#111,#444 50%,#1a1a1a)" role="img" aria-label="Film posters lit on a cinema wall"></div>
<div class="abs hex" style="left:355px;top:948px;width:137px;height:124px;background:var(--red)"></div>
<div class="abs hex" style="left:320px;top:1093px;width:274px;height:248px;background:radial-gradient(circle at 55% 35%,#e0a050,#8a5a2a 55%,#3a2410)" role="img" aria-label="Action film still in a dusty golden haze"></div>
<div class="abs hex" style="left:198px;top:1217px;width:138px;height:125px;background:var(--black)"></div>

<div class="abs about-label">ABOUT US</div>
<div class="abs about-rule"></div>
<div class="abs about-title">VYNTRA</div>
<p class="abs copy about-p1">Lorem ipsum dolor sit amet, consectetur adipiscing elit, sed do eiusmod tempor incididunt ut labore et dolore magna aliqua. Ut enim ad minim veniam, quis nostrud exercitation ullamco laboris nisi ut aliquip ex ea commodo consequat. Duis aute irure dolor in reprehenderit in voluptate velit esse cillum dolore eu fugiat nulla pariatur.</p>
<p class="abs copy about-p2">Excepteur sint occaecat cupidatat non proident, sunt in culpa qui officia deserunt mollit anim id est laborum.</p>
<div class="abs btn about-btn">Learn More</div>

<!-- featured -->
<div class="abs feat-label">AS FEATURED IN</div>
<div class="abs feat-box" style="left:348px"><span class="feat-mark"></span></div>
<div class="abs feat-box" style="left:540px"><span class="feat-mark"></span></div>
<div class="abs feat-box" style="left:732px"><span class="feat-mark"></span></div>
<div class="abs feat-box" style="left:924px"><span class="feat-mark"></span></div>

<!-- services -->
<svg class="abs svc-bg" viewBox="0 0 1200 694" preserveAspectRatio="none">
  <path d="M0 92 Q600 -90 1200 92 L1200 694 L0 694 Z" fill="#f00000"/>
</svg>
<div class="abs svc-title">OUR SERVICES</div>

<div class="abs svc-img" style="left:112px;background:linear-gradient(180deg,#0a1a5a,#2a5acc 55%,#050a20)" role="img" aria-label="Cinema screen in a dark auditorium"></div>
<div class="abs svc-img" style="left:362px;background:linear-gradient(180deg,#2a2218,#6a5840 55%,#3a2e22)" role="img" aria-label="TV on a sideboard in a lamp-lit room"></div>
<div class="abs svc-img" style="left:612px;background:linear-gradient(180deg,#0a2a6a,#3a7acc 50%,#c89a4a)" role="img" aria-label="Popcorn in front of a bright TV screen"></div>
<div class="abs svc-img" style="left:862px;background:linear-gradient(180deg,#4a3a32,#b08a70 50%,#3a2a22)" role="img" aria-label="Friends laughing while watching a film"></div>

<div class="abs svc-card" style="left:125px"><h3>Duis aute irure</h3><p>Lorem ipsum dolor sit amet, consectetur adipiscing elit, sed do eiusmod tempor incididunt ut labore et dolore magna aliqua.</p><span class="btn svc-btn">More Info</span></div>
<div class="abs svc-card" style="left:375px"><h3>Duis aute irure</h3><p>Lorem ipsum dolor sit amet, consectetur adipiscing elit, sed do eiusmod tempor incididunt ut labore et dolore magna aliqua.</p><span class="btn svc-btn">More Info</span></div>
<div class="abs svc-card" style="left:625px"><h3>Duis aute irure</h3><p>Lorem ipsum dolor sit amet, consectetur adipiscing elit, sed do eiusmod tempor incididunt ut labore et dolore magna aliqua.</p><span class="btn svc-btn">More Info</span></div>
<div class="abs svc-card" style="left:875px"><h3>Duis aute irure</h3><p>Lorem ipsum dolor sit amet, consectetur adipiscing elit, sed do eiusmod tempor incididunt ut labore et dolore magna aliqua.</p><span class="btn svc-btn">More Info</span></div>

<!-- tv programs -->
<div class="abs tv-img" role="img" aria-label="Smart TV showing a series menu, hand holding a remote beside a bowl of popcorn"></div>
<div class="abs tv-card">
  <h2>TELEVISION THAT USES THE INTERNET TO DELIVER TV PROGRAMS.</h2>
  <p class="copy">Lorem ipsum dolor sit amet, consectetur adipiscing elit, sed do eiusmod tempor incididunt ut labore et dolore magna aliqua. Ut enim ad minim veniam, quis nostrud exercitation ullamco laboris nisi ut aliquip ex ea commodo consequat. Duis aute irure dolor in reprehenderit in voluptate velit esse cillum dolore eu fugiat nulla pariatur.</p>
  <p class="copy">Excepteur sint occaecat cupidatat non proident, sunt in culpa qui officia deserunt mollit anim id est laborum.</p>
</div>

<!-- subscription -->
<div class="abs sub-title">GET A SUBSCRIPTION</div>
<div class="abs field" style="left:220px;top:3036px;width:234px">User name</div>
<div class="abs field" style="left:487px;top:3036px;width:232px">Password</div>
<div class="abs field" style="left:746px;top:3036px;width:234px">Membership tier</div>
<div class="abs field" style="left:220px;top:3107px;width:371px">Name</div>
<div class="abs field" style="left:609px;top:3107px;width:371px">Payment<span class="card-ico"></span></div>
<div class="abs btn sub-btn">Submit</div>

<!-- footer -->
<svg class="abs foot-shape" viewBox="0 0 1200 456" preserveAspectRatio="none">
  <path d="M0 118 Q600 -20 1200 118 L1200 456 L0 456 Z" fill="#0a0a0a"/>
  <path d="M112 102 Q600 -30 1088 102 Q600 20 112 102 Z" fill="#f00000"/>
</svg>
<div class="abs foot-brand">VYNTRA</div>
<p class="abs foot-text">Lorem ipsum dolor sit amet, consectetur adipiscing elit, sed do eiusmod tempor incididunt ut labore Lorem ipsum dolor sit amet, consectetur adipiscing elit</p>

<div class="abs foot-h" style="left:452px">Services</div>
<ul class="abs foot-list" style="left:452px"><li>Lorem ipsum</li><li>Dolor sit amet,</li><li>Consectetur</li><li>Adipiscing</li><li>Dolor sit amet,</li></ul>

<div class="abs foot-h" style="left:658px">Quick Links</div>
<ul class="abs foot-list" style="left:658px"><li>Home</li><li>About Us</li><li>Blogs</li><li>Team</li><li>Contact us</li></ul>

<div class="abs foot-h" style="left:886px">Contact us</div>
<div class="abs ct-row" style="top:3515px"><span class="ct-ico"><svg width="24" height="24"><path d="M12 5a4 4 0 0 1 4 4c0 3-4 9-4 9s-4-6-4-9a4 4 0 0 1 4-4z" fill="#fff"/></svg></span>123,Lorem ipsum dolor sit consectetur</div>
<div class="abs ct-row" style="top:3577px"><span class="ct-ico"><svg width="24" height="24"><path d="M8 6l3 3-2 2c1 2 3 4 5 5l2-2 3 3-2 2c-6 0-11-5-11-11z" fill="#fff"/></svg></span>+1 888 888 8888</div>
<div class="abs ct-row" style="top:3628px"><span class="ct-ico"><svg width="24" height="24"><rect x="5" y="7" width="14" height="10" fill="#fff"/><path d="M5 7l7 6 7-6" stroke="#f00000" stroke-width="1.5" fill="none"/></svg></span>info@companyname.com</div>

<div class="abs foot-rule"></div>
<div class="abs copyright">© Copyright @2023 Company name | All Rights Reserved</div>

</body>
</html>
```